Infection control

to re-design website to include the benefits of powdered bleach packed in pre-measured sachets which when dissolved in water provides economy, efficacy and is safe to use with the use of costly packaging. We need new text outlining the benefits of the world's most commonly used disinfectant for major hospitals, institutions, pathology, military and disaster areas.

Translate design into coded website using CMS with the following features:
Mobile responsive using HTML 5/ CSS3 standards
Coded with SEO standards and with H1 tags for easy spidering and with Wordpress CMS with is page rank 9
Site migration
Email support
Updates

Target Market(s)

hospitals, institutions, pathology, military and disaster areas

Industry/Entity Type

Chemical Product

Number of Pages Required

4 page

Colors

Designer to choose colors to be used in the design.

Requirements
Must have
• factual information based on the efficiency of sodium hypochlorite (bleach) used for infection control. The many viruses, bacteria, pathogens etc which certain strengths of bleach eliminate upon contact.
• As tis is a redesign, existing pages including MSDS sheets to stay the same
Nice to have
• a new look and feel including current logos
Should not have
• incorrect info

```html
<!DOCTYPE html>
<html lang="en">
<head>
<meta charset="utf-8">
<title>Downloads – Purevia</title>
<link href="https://fonts.googleapis.com/css2?family=Poppins:wght@400;500;600;700&display=swap" rel="stylesheet">
<style>
:root{
  --green:#7cc242;
  --green-dark:#5fa82a;
  --ink:#222;
  --muted:#444;
  --footer-bg:#efefef;
  --line:#d9d9d9;
  --white:#fff;
}
*{box-sizing:border-box;margin:0;padding:0}
html,body{width:922px;height:1200px;overflow:hidden;background:var(--white)}
body{font-family:"Poppins",sans-serif;color:var(--ink);position:relative}
.abs{position:absolute}

/* header */
.site-header{position:absolute;left:0;top:0;width:922px;height:93px;background:var(--white)}
.brand{left:76px;top:14px;display:flex;align-items:center;gap:6px}
.brand-dot{width:34px;height:34px;border-radius:50%;background:var(--green)}
.brand-name{font-size:36px;font-weight:500;color:var(--green);line-height:1}
.tagline{left:78px;top:66px;font-size:10.5px;letter-spacing:.9px;color:var(--ink)}
.contact-chip{display:flex;align-items:center;gap:10px;font-size:12.5px;color:var(--muted);top:17px}
.chip-icon{width:26px;height:26px;border:2px solid var(--green);border-radius:50%;display:flex;align-items:center;justify-content:center}
.main-nav{right:75px;top:60px;display:flex;gap:20px;font-size:12px;font-weight:500;letter-spacing:.6px}
.main-nav a{color:var(--ink);text-decoration:none}
.main-nav a.active{color:var(--green)}

/* hero */
.hero{left:0;top:93px;width:922px;height:300px;background:linear-gradient(90deg,#8ac84f 0%,#7cc242 50%,#86c64c 100%)}
.hero-title{left:0;top:118px;width:922px;text-align:center;font-size:36px;font-weight:700;color:var(--white);letter-spacing:1.5px}
.hero-wave{left:0;top:300px}

/* downloads */
.doc-card{top:450px;width:241px;height:293px;background:linear-gradient(180deg,#f6f6f6,#e9e9e9);box-shadow:0 0 4px rgba(0,0,0,.08)}
.doc-btn{top:767px;width:191px;height:30px;border-radius:15px;background:var(--green);color:var(--white);font-size:12px;font-weight:500;letter-spacing:.8px;display:flex;align-items:center;justify-content:center}

/* footer */
.site-footer{left:0;top:879px;width:922px;height:256px;background:var(--footer-bg)}
.foot-title{top:922px;font-size:17px;font-weight:600;color:var(--ink);letter-spacing:.3px}
.field{width:174px;height:33px;background:var(--white);border:1px solid var(--line);font-size:9px;color:var(--muted);padding:10px 10px}
.submit{left:76px;top:1054px;width:173px;height:32px;background:var(--green-dark);color:var(--white);font-size:11px;font-weight:600;display:flex;align-items:center;justify-content:center}
.info{left:517px;font-size:10px;line-height:16px;color:var(--ink)}
.info-icon{left:498px}
.quick-links{left:723px;top:971px;list-style:none;font-size:9.5px;line-height:17px}
.quick-links li::before{content:"›";display:inline-block;width:15px;color:var(--ink)}

/* bottom bar */
.bottom-brand{left:76px;top:1148px;display:flex;align-items:center;gap:4px}
.bottom-brand .brand-dot{width:16px;height:16px}
.bottom-brand .brand-name{font-size:19px}
.bottom-tag{left:77px;top:1172px;font-size:5.5px;color:var(--ink)}
.copyright{left:0;top:1155px;width:922px;text-align:center;font-size:9.5px;color:var(--ink)}
.social{top:1155px;width:17px;height:17px;border:1.5px solid #333;border-radius:50%}
</style>
</head>
<body>

<header class="site-header">
  <div class="abs brand"><span class="brand-dot"></span><span class="brand-name">Purevia</span></div>
  <div class="abs tagline">Hospital Grade Infection Control</div>

  <div class="abs contact-chip" style="left:490px">
    <span class="chip-icon"><svg width="12" height="12" viewBox="0 0 24 24"><path fill="#7cc242" d="M6.6 10.8a15 15 0 0 0 6.6 6.6l2.2-2.2c.3-.3.7-.4 1-.2 1.1.4 2.3.6 3.6.6.6 0 1 .4 1 1V20c0 .6-.4 1-1 1A17 17 0 0 1 3 4c0-.6.4-1 1-1h3.5c.6 0 1 .4 1 1 0 1.3.2 2.5.6 3.6.1.3 0 .7-.2 1z"/></svg></span>
    1300 555 014
  </div>
  <div class="abs contact-chip" style="left:636px">
    <span class="chip-icon"><svg width="12" height="10" viewBox="0 0 24 18"><rect x="1.5" y="1.5" width="21" height="15" fill="none" stroke="#7cc242" stroke-width="2.5"/><path d="M2 2l10 8 10-8" fill="none" stroke="#7cc242" stroke-width="2.5"/></svg></span>
    hello@purevia-care.com
  </div>

  <nav class="abs main-nav">
    <a href="#">HOME</a><a href="#">ABOUT US</a><a href="#">PRODUCTS</a><a href="#" class="active">DOWNLOADS</a><a href="#">MEDIA &amp; NEWS</a><a href="#">CONTACT US</a>
  </nav>
</header>

<section>
  <div class="abs hero" role="img" aria-label="Photo of smiling medical staff in a hospital, tinted green"></div>
  <h1 class="abs hero-title">DOWNLOADS</h1>
  <svg class="abs hero-wave" width="922" height="100" viewBox="0 0 922 100">
    <path d="M0 62 C140 10 330 8 520 48 C680 80 820 62 922 45 L922 100 L0 100 Z" fill="#7cc242"/>
    <path d="M0 76 C150 22 340 22 520 58 C680 88 820 72 922 54 L922 100 L0 100 Z" fill="#fff"/>
  </svg>
</section>

<main>
  <div class="abs doc-card" style="left:76px" role="img" aria-label="Preview of the Chlorex 500 safety data sheet"></div>
  <div class="abs doc-card" style="left:340px" role="img" aria-label="Preview of the Chlorex 5000 safety data sheet"></div>
  <div class="abs doc-card" style="left:603px" role="img" aria-label="Preview of the blood spill guidelines sheet"></div>

  <a class="abs doc-btn" style="left:101px">MSDS - CHLOREX 500 ®</a>
  <a class="abs doc-btn" style="left:365px">MSDS - CHLOREX 5000 ®</a>
  <a class="abs doc-btn" style="left:628px">BLOOD SPILL GUIDELINES</a>
</main>

<footer>
  <div class="abs site-footer"></div>

  <h2 class="abs foot-title" style="left:76px">GET A QUICK NOW!</h2>
  <div class="abs field" style="left:76px;top:970px">Your Name</div>
  <div class="abs field" style="left:260px;top:970px">Your E - Mail</div>
  <div class="abs field" style="left:76px;top:1009px">Your Phone</div>
  <div class="abs field" style="left:260px;top:1010px">Message</div>
  <div class="abs submit">SUBMIT</div>

  <h2 class="abs foot-title" style="left:497px">CONTACT US</h2>
  <svg class="abs info-icon" style="top:973px" width="9" height="12" viewBox="0 0 12 16"><path d="M6 0a6 6 0 0 0-6 6c0 4.5 6 10 6 10s6-5.5 6-10a6 6 0 0 0-6-6z" fill="#7cc242"/><circle cx="6" cy="6" r="2.3" fill="#efefef"/></svg>
  <div class="abs info" style="top:967px">Northgate Supplies P.O. Box 4418<br>Fairview, CT 06100</div>
  <svg class="abs info-icon" style="top:1012px" width="11" height="11" viewBox="0 0 24 24"><path fill="#7cc242" d="M6.6 10.8a15 15 0 0 0 6.6 6.6l2.2-2.2c.3-.3.7-.4 1-.2 1.1.4 2.3.6 3.6.6.6 0 1 .4 1 1V20c0 .6-.4 1-1 1A17 17 0 0 1 3 4c0-.6.4-1 1-1h3.5c.6 0 1 .4 1 1 0 1.3.2 2.5.6 3.6.1.3 0 .7-.2 1z"/></svg>
  <div class="abs info" style="top:1009px;left:518px;font-size:10.5px">Phone:1300 555 014<br>Fax : 1300 555 015</div>
  <svg class="abs info-icon" style="top:1051px" width="10" height="8" viewBox="0 0 24 18"><rect width="24" height="18" fill="#7cc242"/><path d="M1 1l11 8 11-8" fill="none" stroke="#efefef" stroke-width="2"/></svg>
  <div class="abs info" style="top:1047px">hello@purevia-care.com</div>

  <h2 class="abs foot-title" style="left:723px">QUICK LINK</h2>
  <ul class="abs quick-links">
    <li>Home</li><li>About</li><li>Products</li><li>Downloads</li><li>Media &amp; News</li><li>Contact Us</li>
  </ul>

  <div class="abs bottom-brand"><span class="brand-dot"></span><span class="brand-name">Purevia</span></div>
  <div class="abs bottom-tag">Hospital Grade Infection Control</div>
  <div class="abs copyright">©2018 Purevia. All Rights Reserved</div>
  <span class="abs social" style="left:765px"></span>
  <span class="abs social" style="left:786px"></span>
  <span class="abs social" style="left:807px"></span>
  <span class="abs social" style="left:828px"></span>
</footer>

</body>
</html>
```